Brindlewick Solutions Ltd

I'd like to create a company letterhead for the attached logo in word format.

I'd like to emphasis the icon in large translucent state from the left corner and ensure that the letterhead colouring matches the colour palette of the current logo with a contrast so it's clear to see. I've attached a copy of our sister company page on the app for reference.

```html
<!DOCTYPE html>
<html lang="en">
<head>
<meta charset="utf-8">
<title>Brindlewick Solutions Ltd – Letterhead</title>
<link href="https://fonts.googleapis.com/css2?family=Lato:wght@400&family=Montserrat:wght@400;500&display=swap" rel="stylesheet">
<style>
  :root {
    --brand-teal: #00b9a6;
    --brand-teal-line: #3cc7b7;
    --paper: #ffffff;
    --backdrop: #b3b3b3;
  }
  * { box-sizing: border-box; margin: 0; padding: 0; }
  html, body {
    width: 1200px; height: 1200px; overflow: hidden;
    background: var(--backdrop);
    font-family: "Montserrat", Arial, sans-serif;
  }
  .letterhead {
    position: absolute; left: 160px; top: 30px;
    width: 881px; height: 1140px;
    background: var(--paper);
    color: var(--brand-teal);
    overflow: hidden;
  }
  .header-band {
    position: absolute; left: 0; top: 0; width: 100%; height: 76px;
    background: var(--brand-teal);
  }
  .brand-disc {
    position: absolute; left: 386px; top: 14px; width: 108px; height: 108px;
    border-radius: 50%; background: var(--paper);
  }
  .brand-name {
    position: absolute; left: 0; top: 130px; width: 100%;
    text-align: center; font-size: 34px; font-weight: 400;
    color: var(--brand-teal); letter-spacing: 0.5px;
  }
  .letter-content {
    position: absolute; left: 65px; top: 268px; width: 752px;
  }
  .salutation {
    font-size: 18px; font-weight: 500; line-height: 22px;
    margin-bottom: 44px;
  }
  .letter-body p {
    font-family: "Lato", Arial, sans-serif;
    font-size: 14.4px; line-height: 23.6px;
    text-align: justify; hyphens: auto; -webkit-hyphens: auto;
    margin-bottom: 25px;
  }
  .letter-body p:last-child { margin-bottom: 0; }
  .sign-off { margin-top: 28px; }
  .signer-name { font-size: 19px; font-weight: 500; line-height: 22px; }
  .signer-role { font-size: 14px; line-height: 18px; }
  .signature-area {
    margin-top: 30px; width: 220px; height: 68px;
    background: linear-gradient(90deg, rgba(42,42,42,0.06), rgba(42,42,42,0.14), rgba(42,42,42,0.05));
    border-radius: 4px;
  }
  .footer-contacts {
    position: absolute; left: 0; top: 1046px; width: 100%; height: 18px;
    font-size: 15.5px; line-height: 18px;
    display: flex; justify-content: center; align-items: center; gap: 6px;
  }
  .footer-contacts svg { width: 10px; height: 10px; }
  .footer-rule {
    position: absolute; left: 0; top: 1070px; width: 100%; height: 18px;
    display: flex; align-items: center; font-size: 15px; line-height: 18px;
  }
  .footer-rule::before, .footer-rule::after {
    content: ""; flex: 1; height: 1px; background: var(--brand-teal-line);
  }
  .footer-rule span { padding: 0 2px; }
  .footer-address {
    position: absolute; left: 0; top: 1090px; width: 100%;
    text-align: center; font-size: 15.5px; line-height: 18px;
  }
</style>
</head>
<body>
<main class="letterhead">
  <div class="header-band"></div>
  <div class="brand-disc"></div>
  <div class="brand-name">Brindlewick Solutions Ltd</div>

  <div class="letter-content">
    <div class="salutation">Dear sir/Madam,</div>

    <section class="letter-body">
      <p>Lorem Ipsum is simply dummy text of the printing and typesetting industry. Lorem Ipsum has been the industry's standard dummy text ever since the 1500s, when an unknown printer took a galley of type and scrambled it to make a type specimen book. It has survived not only five centuries, but also the leap into electronic typesetting, remaining essentially unchanged. It was popularised in the 1960s with the release of Letrafix</p>
      <p>Contrary to popular belief, Lorem Ipsum is not simply random text. It has roots in a piece of classical Latin literature from 45 BC, making it over 2000 years old. Harold Wexley, a Latin professor at Marlow Ridge College in Vermont, looked up one of the more obscure Latin words, consectetur, from a Lorem Ipsum passage, and going through the cites of the word in classical literature, discovered the undoubtable source. Lorem Ipsum comes from sections 1.10.32 and 1.10.33 of "de Finibus Bonorum et Malorum" (The Extremes of Good and Evil) by Aurelian Tesso, written in 45 BC. This book is a treatise on the theory of ethics, very popular during the Renaissance. The first line of Lorem Ipsum, "Lorem ipsum dolor sit amet..", comes from a line in section 1.10.32. typesetting, remaining essentially unchanged. It was popularised in the 1960s with the release of Letrafix</p>
      <p>Lorem Ipsum is simply dummy text of the printing and typesetting industry. Lorem Ipsum has been the industry's standard dummy text ever since the 1500s, when an unknown printer took a galley of type and scrambled it to make a type specimen book. It has survived not only five centuries, but also the leap into electronic typesetting, remaining essentially unchanged. It was popularised in the 1960s with the release of Letrafix</p>
    </section>

    <div class="sign-off">
      <div class="signer-name">Daniel R. Moore, Esq.</div>
      <div class="signer-role">Managing Attorney</div>
    </div>
    <div class="signature-area" role="img" aria-label="Handwritten signature"></div>
  </div>

  <div class="footer-contacts">
    <svg viewBox="0 0 10 10"><path d="M2 0.5 L3.6 2.6 L2.7 3.6 Q3.6 5.8 6.2 7.3 L7.2 6.4 L9.5 8 L8.3 9.5 Q2.5 8.5 0.5 1.7 Z" fill="var(--brand-teal)"/></svg>
    <span>01632 960 418</span>
    <svg viewBox="0 0 10 10"><rect x="0.7" y="2" width="8.6" height="6" fill="none" stroke="var(--brand-teal)" stroke-width="1"/><path d="M0.7 2 L5 5.5 L9.3 2" fill="none" stroke="var(--brand-teal)" stroke-width="1"/></svg>
    <span>info@brindlewick.co.uk</span>
    <svg viewBox="0 0 10 10"><circle cx="5" cy="5" r="4.3" fill="none" stroke="var(--brand-teal)" stroke-width="1"/><path d="M0.7 5 H9.3 M5 0.7 Q2.5 5 5 9.3 M5 0.7 Q7.5 5 5 9.3" fill="none" stroke="var(--brand-teal)" stroke-width="0.8"/></svg>
    <span>www.brindlewick.co.uk</span>
  </div>
  <div class="footer-rule"><span>BRINDLEWICK</span></div>
  <div class="footer-address">31 Alder Crescent, 1st Floor, Glasgow, G2 7QX</div>
</main>
</body>
</html>
```